Veltra Metrics New Website for Health Benefits Plan Decisioneering Tool Launch

Veltra Metrics is a SaaS provider of health benefits comparison tools. We need a new simple SaaS focused website to direct customers to our product

Target Market(s)

General Public comparing their health benefits plans from their employer or from the state exchanges in the US

Coding

Coded - Design and coding required

Number of Pages Required

3 page

Requirements
Must have
• Main page - "Know the Best Health Benefits Plan for You!"
Graphic of a person looking over papers on their desk
Compare Now button to link to SaaS product
About Us
Product Page

https://plimbo.example/top-app-pages/

```html
<!DOCTYPE html>
<html lang="en">
<head>
<meta charset="utf-8">
<title>Veltra Metrics – Health Benefits Plan Comparison</title>
<link rel="stylesheet" href="https://fonts.googleapis.com/css2?family=Roboto:wght@400;500;700&display=swap">
<style>
:root{
  --blue:#2aa9e0;
  --green:#47d296;
  --grad:linear-gradient(90deg,#2aa9e0,#47d296);
  --ink:#111;
  --body:#333;
  --muted:#555;
  --grey-band:#ebedef;
  --white:#fff;
  --nav-active:#2aa9e0;
  --rule:#e2e2e2;
}
*{box-sizing:border-box;margin:0;padding:0}
html,body{width:1200px;height:3088px;overflow:hidden;background:var(--white)}
body{position:relative;font-family:'Roboto',sans-serif;color:var(--body)}
.abs{position:absolute}
.btn{position:absolute;display:flex;align-items:center;justify-content:center;background:var(--grad);color:var(--white);font-weight:500;font-size:17px;text-decoration:none;border-radius:3px;box-shadow:0 3px 8px rgba(42,169,224,.25);z-index:2}
.brand{font-weight:400;font-size:24px;color:var(--blue);letter-spacing:.5px;display:flex;align-items:center;gap:10px}
.brand-dot{width:14px;height:14px;border-radius:50%;background:var(--blue)}
.nav a{position:absolute;top:42px;font-size:15px;color:var(--ink);text-decoration:none}
.nav a.active{color:var(--nav-active)}
.hero-title{left:94px;top:192px;font-size:43px;line-height:58px;font-weight:700;color:var(--ink);z-index:3;white-space:nowrap}
.art{position:absolute;border-radius:40% 55% 45% 50%;z-index:1}
.card{position:absolute;width:248px;height:274px;background:var(--white);box-shadow:0 0 14px rgba(42,169,224,.22);text-align:center;padding-top:14px}
.card svg{display:block;margin:0 auto}
.card h3{font-size:15px;font-weight:500;color:var(--ink);margin-top:20px}
.card p{font-size:13.5px;line-height:21.5px;color:var(--muted);margin:12px auto 0;width:150px}
.section-title{font-size:35px;font-weight:500;color:var(--ink)}
.para{font-size:16px;line-height:24px;color:var(--body)}
.stats{left:0;top:1322px;width:1200px;height:282px;background:var(--grad)}
.stat{position:absolute;top:40px;width:228px;height:180px;text-align:center;color:var(--white)}
.stat svg{position:absolute;left:0;top:0}
.stat strong{position:relative;display:block;font-size:44px;font-weight:700;padding-top:34px}
.stat span{position:relative;display:block;font-size:20px;font-weight:700;margin-top:6px}
.band{left:0;top:2184px;width:1200px;height:378px;background:var(--grey-band)}
.contact-card{left:110px;top:2148px;width:442px;height:450px;background:linear-gradient(135deg,#2aa9e0,#47d296);color:var(--white);padding:62px 0 0 33px}
.contact-card h2{font-size:34px;font-weight:700;letter-spacing:.5px}
.c-item{position:absolute;left:33px;display:flex;gap:16px}
.c-item h4{font-size:21px;font-weight:700}
.c-item p{font-size:15.5px;line-height:19px;margin-top:4px}
.field{position:absolute;background:var(--white);border-radius:3px;font-size:12.5px;color:#444;padding:14px 14px}
.footer-text{font-size:15px;line-height:19px;color:var(--body)}
.qlinks a{position:absolute;left:590px;font-size:15px;color:var(--body);text-decoration:none}
.social{position:absolute;top:2769px;width:34px;height:34px;border-radius:50%;background:var(--grad)}
</style>
</head>
<body>

<header>
  <div class="abs brand" style="left:112px;top:30px"><span class="brand-dot"></span>Veltra Metrics</div>
  <nav class="nav">
    <a class="active" style="left:414px">HOME</a>
    <a style="left:508px">ABOUT US</a>
    <a style="left:630px">PRODUCT</a>
    <a style="left:752px">SERVICES</a>
    <a style="left:871px">BENEFITS</a>
  </nav>
  <a class="btn" href="https://plimbo.example/top-app-pages/" style="left:961px;top:24px;width:142px;height:48px;font-size:15px">COMPARE NOW</a>
</header>

<section class="hero">
  <h1 class="abs hero-title">KNOW THE BEST HEALTH<br>BENEFITS PLAN<br>FOR YOU!</h1>
  <a class="btn" style="left:95px;top:390px;width:161px;height:54px">LEARN MORE</a>
  <div class="art" role="img" aria-label="Illustration of a team working around a large monitor with a clock, gears and puzzle pieces" style="left:560px;top:120px;width:568px;height:354px;background:linear-gradient(135deg,#d4ecef,#a9d8e4 55%,#f3d98a)"></div>
</section>

<section class="features">
  <div class="card" style="left:89px;top:532px">
    <svg width="84" height="90" viewBox="0 0 84 90" fill="none" stroke="#2aa9e0" stroke-width="2.5"><rect x="4" y="20" width="60" height="44" rx="3"/><path d="M24 76h20M34 64v12M12 32h20M12 40h36M12 48h30"/><circle cx="64" cy="20" r="12"/><circle cx="64" cy="20" r="5"/></svg>
    <h3>MULTIPLY PRODUCTIVITY</h3>
    <p>Lorem ipsum dolor sit amet, consectetur adipiscing elit</p>
  </div>
  <div class="card" style="left:373px;top:634px">
    <svg width="96" height="96" viewBox="0 0 96 96" fill="none" stroke="#2aa9e0" stroke-width="2.5"><rect x="4" y="22" width="62" height="52" rx="3"/><circle cx="26" cy="46" r="12"/><path d="M26 38v16M44 40h14M44 48h14M44 56h14M26 74v14M16 88h20"/><rect x="50" y="4" width="42" height="34"/><path d="M58 32v-10M68 32v-16M78 32v-20M86 92V50M80 58l6-8 6 8M8 10h30M32 4l6 6-6 6"/></svg>
    <h3>REPORTED DATA</h3>
    <p>Lorem ipsum dolor sit amet, consectetur adipiscing elit</p>
  </div>
  <div class="card" style="left:89px;top:847px">
    <svg width="84" height="84" viewBox="0 0 84 84" fill="none" stroke="#2aa9e0" stroke-width="2.5"><rect x="14" y="6" width="56" height="66" rx="3"/><circle cx="42" cy="28" r="14"/><rect x="36" y="26" width="12" height="10"/><path d="M38 26v-4a4 4 0 018 0v4M22 54h40M2 20h12M70 20h12M2 64h12M70 64h12"/><circle cx="30" cy="54" r="5"/><circle cx="54" cy="54" r="5"/></svg>
    <h3>ENHANCE SECURITY</h3>
    <p>Lorem ipsum dolor sit amet, consectetur adipiscing elit</p>
  </div>
  <div class="card" style="left:373px;top:949px">
    <svg width="70" height="84" viewBox="0 0 70 84"><defs><linearGradient id="dbg" x1="0" x2="1"><stop offset="0" stop-color="#2aa9e0"/><stop offset="1" stop-color="#47d296"/></linearGradient></defs><g fill="url(#dbg)"><rect x="4" y="6" width="62" height="16" rx="4"/><rect x="4" y="26" width="62" height="16" rx="4"/><rect x="4" y="46" width="62" height="16" rx="4"/><rect x="4" y="66" width="62" height="16" rx="4"/></g><g fill="#fff"><rect x="12" y="12" width="30" height="3"/><rect x="12" y="32" width="30" height="3"/><rect x="12" y="52" width="30" height="3"/><rect x="12" y="72" width="30" height="3"/></g></svg>
    <h3>DATA STORAGE</h3>
    <p>Lorem ipsum dolor sit amet, consectetur adipiscing elit</p>
  </div>
</section>

<section class="about">
  <h2 class="abs section-title" style="left:698px;top:736px">ABOUT US</h2>
  <p class="abs para" style="left:698px;top:792px;width:430px">Lorem ipsum dolor sit amet, consectetur adipiscing elit, sed do eiusmod tempor incididunt ut labore et dolore magna aliqua. Ut enim ad minim veniam, quis nostrud exercitation ullamco laboris nisi ut aliquip ex ea commodo consequat Duis aute irure dolor in reprehenderit in voluptate velit esse cillum dolore eu fugiat nulla pariatur. Excepteur sint occaecat cupidatat non proident, sunt in culpa qui officia deserunt mollit anim id est laborum."</p>
  <a class="btn" style="left:700px;top:1008px;width:160px;height:54px">LEARN MORE</a>
</section>

<section class="abs stats">
  <div class="stat" style="left:117px"><svg width="228" height="180" viewBox="0 0 228 180"><path d="M40 10C100-10 180 10 210 60s10 110-30 116S120 130 70 140 0 110 10 70 10 20 40 10z" fill="#2aa9e0" opacity=".65"/></svg><strong>6000+</strong><span>Complete Project</span></div>
  <div class="stat" style="left:363px"><svg width="228" height="180" viewBox="0 0 228 180"><path d="M40 10C100-10 180 10 210 60s10 110-30 116S120 130 70 140 0 110 10 70 10 20 40 10z" fill="#2aa9e0" opacity=".65"/></svg><strong>4500+</strong><span>Awarded Projects</span></div>
  <div class="stat" style="left:610px"><svg width="228" height="180" viewBox="0 0 228 180"><path d="M40 10C100-10 180 10 210 60s10 110-30 116S120 130 70 140 0 110 10 70 10 20 40 10z" fill="#2aa9e0" opacity=".6"/></svg><strong>5500+</strong><span>Complete Project</span></div>
  <div class="stat" style="left:856px"><svg width="228" height="180" viewBox="0 0 228 180"><path d="M40 10C100-10 180 10 210 60s10 110-30 116S120 130 70 140 0 110 10 70 10 20 40 10z" fill="#2aa9e0" opacity=".5"/></svg><strong>6000+</strong><span>Complete Project</span></div>
</section>

<section class="video">
  <h2 class="abs section-title" style="left:157px;top:1732px">VELTRA VIDEO</h2>
  <p class="abs para" style="left:157px;top:1788px;width:430px">Lorem ipsum dolor sit amet, consectetur adipiscing elit, sed do eiusmod tempor incididunt ut labore et dolore magna aliqua. Ut enim ad minim veniam, quis nostrud exercitation ullamco laboris nisi ut aliquip ex ea commodo consequat Duis aute irure dolor in reprehenderit in voluptate velit esse cillum dolore eu fugiat nulla pariatur. Excepteur sint occaecat cupidatat non proident, sunt in culpa qui officia deserunt mollit anim id est laborum."</p>
  <a class="btn" style="left:157px;top:2004px;width:161px;height:54px">LEARN MORE</a>
  <div class="art" role="img" aria-label="Illustration of a person at a desk working on a computer, with a play button over it" style="left:672px;top:1752px;width:360px;height:294px;border-radius:8px;background:linear-gradient(160deg,#e6f4fc,#9fd0f3 60%,#f3c6c6)"></div>
  <svg class="abs" style="left:831px;top:1876px;z-index:2" width="44" height="44" viewBox="0 0 44 44" fill="none" stroke="#222" stroke-width="2"><circle cx="22" cy="22" r="20"/><path d="M17 13l13 9-13 9z"/></svg>
</section>

<section class="contact">
  <div class="abs band"></div>
  <div class="abs contact-card">
    <h2>CONTACT US</h2>
    <div class="c-item" style="top:124px">
      <svg width="32" height="42" viewBox="0 0 32 42" fill="none" stroke="#fff" stroke-width="2"><path d="M16 40S3 24 3 15a13 13 0 0126 0c0 9-13 25-13 25z"/><circle cx="16" cy="15" r="5"/></svg>
      <div><h4>Visit us</h4><p style="margin-left:4px">105 street name<br>city name<br>country name</p></div>
    </div>
    <div class="c-item" style="top:250px">
      <svg width="36" height="36" viewBox="0 0 36 36" fill="none" stroke="#fff" stroke-width="2"><path d="M8 2l6 8-4 4c2 5 6 9 11 11l4-4 8 6-4 7C15 34 2 21 2 7z"/></svg>
      <div><h4>Phone</h4><p>555-555-5555</p></div>
    </div>
    <div class="c-item" style="top:330px">
      <svg width="38" height="30" viewBox="0 0 38 30" fill="none" stroke="#fff" stroke-width="2"><rect x="1" y="1" width="36" height="28"/><path d="M1 1l18 16L37 1M1 29l13-14M37 29L24 15"/></svg>
      <div><h4>Email</h4><p>hello@veltrametrics.example</p></div>
    </div>
  </div>
  <div class="field" style="left:646px;top:2222px;width:219px;height:42px">Name</div>
  <div class="field" style="left:882px;top:2222px;width:220px;height:42px">Email</div>
  <div class="field" style="left:646px;top:2282px;width:219px;height:42px">Phone number</div>
  <div class="field" style="left:882px;top:2282px;width:220px;height:42px">Subject</div>
  <div class="field" style="left:648px;top:2342px;width:456px;height:111px">Message</div>
  <a class="btn" style="left:776px;top:2478px;width:161px;height:54px">SUBMIT</a>
</section>

<footer>
  <div class="abs brand" style="left:181px;top:2728px"><span class="brand-dot"></span>Veltra Metrics</div>
  <p class="abs footer-text" style="left:181px;top:2797px;width:245px">Lorem ipsum dolor sit amet, consectetur adipiscing elit, sed do eiusmod tempor incididunt ut labore et dolore magna aliqua</p>
  <h4 class="abs" style="left:588px;top:2730px;font-size:18px;font-weight:500;color:var(--ink)">QUICK LINK</h4>
  <nav class="qlinks">
    <a style="top:2768px">HOME</a>
    <a style="top:2798px">ABOUT US</a>
    <a style="top:2828px">PRODUCT</a>
    <a style="top:2858px">SERVICES</a>
    <a style="top:2888px">BENEFITS</a>
  </nav>
  <h4 class="abs" style="left:855px;top:2730px;font-size:18px;font-weight:500;color:var(--ink)">FOLLOW US</h4>
  <span class="social" style="left:855px"></span>
  <span class="social" style="left:893px"></span>
  <span class="social" style="left:931px"></span>
  <span class="social" style="left:969px"></span>
  <div class="abs" style="left:110px;top:2977px;width:980px;height:1px;background:var(--rule)"></div>
  <p class="abs" style="left:0;top:3022px;width:1206px;text-align:center;font-size:15px;color:var(--body)">© Veltra Metrics All Rights Reserved</p>
</footer>

</body>
</html>
```